Etiketten für Bio Seifen
Zielgruppe
Wir stellen hochwertig 'handgemachte' Bio-Seifen her. Die Zielgruppe ist von 3-99 Jahren und zusätzlich haben wir auch noch Seife für Hunde.
Der Firmenname ist 'Verdolina'
Aufgabenstellung
Das Etikett soll Bezug auf Natur, Bio, Nachhaltigkeit nehmen. Wir stellen uns 'weiche' Aquarellfarben vor...Seife: Lavendel, Calendular, 7 Kräuter etc.
Das Etikett soll auf eine Beutelschachtel. Die Schachtel hat eine Anmaße: Breite 55mm; Höhe 120mm; Tiefe 30mm
Das Etikett soll im vorderen- und hinteren Bereich zusammenhängend geklebt werden.
Das Etikett soll eine Abmaße von: Breite 51mm; Höhe 114mm haben (Vorderseite) Rückseite gleich.
Wir möchten die Produkte auch gerne nummerieren, d.h. jede Seife hat eine Nummer die nicht zu groß dargestellt werden soll aber trotzdem gut leserlich.
Wir haben noch ein paar Bilder hochgeladen wie wir uns das ungefähr vorstellen.

```html
<!DOCTYPE html>
<html lang="de">
<head>
<meta charset="utf-8">
<title>Verdolina – Handgemachte Seife Lavendel</title>
<link rel="stylesheet" href="https://fonts.googleapis.com/css2?family=Josefin+Sans:wght@400;600;700&family=Kaushan+Script&display=swap">
<style>
  :root {
    --teal: #2a8a7c;
    --teal-dark: #237a6d;
    --paper: #f4f2ee;
    --paper-edge: #eeece8;
    --blush: #f2b4a8;
    --coral: #ec7d72;
    --mint: #a9dcc6;
    --lime: #dfe3a0;
    --lilac: #b3a6e6;
  }
  * { margin: 0; padding: 0; box-sizing: border-box; }
  html, body { width: 1200px; height: 2668px; overflow: hidden; background: var(--paper); }
  .label {
    position: relative;
    width: 1200px;
    height: 2668px;
    overflow: hidden;
    background: var(--paper);
  }
  .floral-background {
    position: absolute;
    inset: 0;
    background:
      radial-gradient(circle at 18% 16%, rgba(236,125,114,0.55) 0 10%, transparent 22%),
      radial-gradient(circle at 85% 14%, rgba(236,125,114,0.55) 0 8%, transparent 18%),
      radial-gradient(circle at 22% 40%, rgba(242,180,168,0.7) 0 12%, transparent 26%),
      radial-gradient(circle at 76% 32%, rgba(220,80,80,0.45) 0 7%, transparent 16%),
      radial-gradient(circle at 35% 22%, rgba(179,166,230,0.6) 0 5%, transparent 14%),
      radial-gradient(circle at 60% 10%, rgba(169,220,198,0.7) 0 8%, transparent 20%),
      radial-gradient(circle at 90% 55%, rgba(242,180,168,0.6) 0 8%, transparent 18%),
      radial-gradient(circle at 8% 72%, rgba(236,125,114,0.5) 0 8%, transparent 18%),
      radial-gradient(circle at 55% 92%, rgba(242,180,168,0.65) 0 12%, transparent 26%),
      radial-gradient(circle at 10% 95%, rgba(169,220,198,0.7) 0 10%, transparent 22%),
      radial-gradient(circle at 90% 88%, rgba(223,227,160,0.7) 0 10%, transparent 22%),
      linear-gradient(160deg, #cfe9dc 0%, #f3ddd3 35%, #e4eecf 60%, #f3d6cf 85%, #cfe9dc 100%);
  }
  .number-tab {
    position: absolute;
    left: 477px;
    top: -4px;
    width: 248px;
    height: 491px;
    background: var(--paper);
    border: 4px solid var(--teal);
    display: flex;
    justify-content: center;
  }
  .number-badge {
    margin-top: 180px;
    width: 122px;
    height: 122px;
    border-radius: 50%;
    background: var(--teal);
    color: #fff;
    font-family: "Josefin Sans", sans-serif;
    font-weight: 600;
    font-size: 38px;
    display: flex;
    align-items: center;
    justify-content: center;
    padding-top: 6px;
  }
  .title-panel {
    position: absolute;
    left: 135px;
    top: 1216px;
    width: 928px;
    height: 884px;
    background: rgba(244,242,238,0.93);
    border: 3px solid var(--teal);
    text-align: center;
    color: var(--teal);
    font-family: "Josefin Sans", sans-serif;
  }
  .product-type {
    margin-top: 130px;
    font-size: 48px;
    font-weight: 400;
    letter-spacing: 6px;
    line-height: 66px;
  }
  .product-name {
    margin-top: 60px;
    font-family: "Kaushan Script", cursive;
    font-size: 124px;
    font-weight: 400;
    line-height: 1;
    color: var(--teal-dark);
  }
  .brand-name {
    margin-top: 248px;
    font-size: 52px;
    font-weight: 700;
    letter-spacing: 7px;
  }
  .batch-year {
    margin-top: 40px;
    font-size: 40px;
    font-weight: 600;
    letter-spacing: 4px;
  }
</style>
</head>
<body>
  <main class="label">
    <div class="floral-background" role="img" aria-label="Aquarell-Blumenmuster mit Lavendelzweigen, rosa und roten Blüten und mintgrünen Blättern"></div>

    <div class="number-tab">
      <div class="number-badge">No 7</div>
    </div>

    <section class="title-panel">
      <p class="product-type">HANDGEMACHTE<br>SEIFE</p>
      <h1 class="product-name">Lavendel</h1>
      <p class="brand-name">VERDOLINA</p>
      <p class="batch-year">2022</p>
    </section>
  </main>
</body>
</html>
```